Tech business card design

We need an amazing business card design for our new business 'Pexla' a marketing tech startup based in Sydney, Australia. We provide an online marketplace for businesses to search and buy advertising media, connect with service providers and learn more about marketing. We wish to communicate 'cool tech', reliability and professionalism and design based around our logo.

Target Market(s)

Business Owners

Contact Information for Business Card

Name
Position
Email Address
Website
Phone Number

Font styles to use
Other font styles liked:
• Avenir & Avenir Next

Colors

Designer to choose colors to be used in the design.

```html
<!DOCTYPE html>
<html lang="en">
<head>
<meta charset="utf-8">
<title>Pexla Business Card</title>
<link href="https://fonts.googleapis.com/css2?family=Nunito+Sans:wght@400;700;800;900&display=swap" rel="stylesheet">
<style>
  :root {
    --navy: #1f1f5c;
    --paper: #ffffff;
    --backdrop: #2b2d31;
    --ink: #1f1f5c;
  }
  * { box-sizing: border-box; margin: 0; padding: 0; }
  html, body {
    width: 1200px;
    height: 900px;
    overflow: hidden;
    background: var(--backdrop);
    font-family: "Nunito Sans", "Avenir Next", sans-serif;
  }
  .canvas {
    position: relative;
    width: 1200px;
    height: 900px;
  }
  .card {
    position: absolute;
    width: 510px;
    height: 300px;
    border-radius: 6px;
    overflow: hidden;
    box-shadow: 0 18px 40px rgba(0,0,0,0.45);
  }
  .card--front {
    left: 70px;
    top: 380px;
    background: var(--paper);
    color: var(--ink);
  }
  .card--back {
    left: 620px;
    top: 220px;
    background: var(--navy);
  }
  .wordmark {
    font-weight: 900;
    letter-spacing: -2px;
    line-height: 1;
    position: absolute;
  }
  .wordmark .tm {
    font-size: 11px;
    font-weight: 900;
    letter-spacing: 0;
    position: absolute;
    right: -4px;
    bottom: -12px;
  }
  .card--front .wordmark {
    left: 34px;
    top: 14px;
    font-size: 84px;
    color: var(--navy);
  }
  .card--back .wordmark {
    left: 50%;
    top: 50%;
    transform: translate(-50%, -56%);
    font-size: 112px;
    color: var(--paper);
  }
  .sweep {
    position: absolute;
    inset: 0;
    width: 100%;
    height: 100%;
  }
  .contact {
    position: absolute;
    left: 110px;
    top: 168px;
    font-size: 14px;
    line-height: 1.3;
    color: var(--ink);
  }
  .contact .name {
    font-weight: 800;
    font-size: 16px;
  }
  .contact .role {
    font-weight: 700;
    margin-bottom: 8px;
  }
  .contact .line {
    font-weight: 800;
  }
</style>
</head>
<body>
<main class="canvas">
  <section class="card card--front" aria-label="Business card front">
    <div class="wordmark">pexla<span class="tm">TM</span></div>
    <svg class="sweep" viewBox="0 0 510 300" aria-hidden="true">
      <path d="M0 142 C 180 128, 400 150, 510 250" fill="none" stroke="var(--navy)" stroke-width="2"/>
    </svg>
    <div class="contact">
      <p class="name">Marcus Dale</p>
      <p class="role">Founder, Director</p>
      <p class="line">+61 (0)412 580 263</p>
      <p class="line">marcus@pexlamedia.com.au</p>
      <p class="line">www.pexlamedia.com.au</p>
    </div>
  </section>

  <section class="card card--back" aria-label="Business card back">
    <div class="wordmark">pexla<span class="tm">TM</span></div>
  </section>
</main>
</body>
</html>
```